Animal Eye Clinic needs a Business card

We are a new veterinary ophthalmology practice (Ridgeline Pet Vision Care) and we need a business card designed. We only see animal eyes - we are not a regular veterinary clinic. We already have a logo. We are looking for a professional, good looking business card to hand out to our clients. We are looking for something simple but professional and contemporary. Our logo is likely the only picture/graphic that needs to be on the card.
Updates

Contact Information for Business Card

Delia Vossman, BSc, DVM, MSc, DipACVO
Veterinary Ophthalmologist

Phone: 250.418.3927
Email: ridgelinepetvisioncare@mailbox-example.net
Website: ridgelinepetvisioncare-example.net
Address: 1874 Thornbury Rd
Kelowna, BC, V1X 4M9

Colors

Designer to choose colors to be used in the design.

Requirements
Must have
• Our logo (attached)

```html
<!DOCTYPE html>
<html lang="en">
<head>
<meta charset="utf-8">
<title>Ridgeline Pet Vision Care – Business Card</title>
<link href="https://fonts.googleapis.com/css2?family=Arimo:wght@400;700&display=swap" rel="stylesheet">
<style>
  :root {
    --teal: #1597a8;
    --teal-deep: #10899a;
    --white: #ffffff;
    --grey: #6f6f6f;
    --stage: #e6e8ea;
    --shadow: rgba(20, 30, 40, 0.22);
  }
  * { box-sizing: border-box; margin: 0; padding: 0; }
  html, body {
    width: 1200px; height: 800px; overflow: hidden;
    background: var(--stage);
    font-family: "Arimo", Arial, sans-serif;
  }
  .stage {
    width: 1200px; height: 800px;
    display: flex; align-items: center; justify-content: center; gap: 48px;
  }
  .card {
    width: 532px; height: 304px;
    border-radius: 18px;
    box-shadow: 0 14px 34px var(--shadow);
    position: relative; overflow: hidden;
  }
  .card--front {
    background: var(--white);
    display: flex; align-items: center; justify-content: center;
  }
  .brand { display: flex; align-items: center; gap: 16px; }
  .brand__dot {
    width: 58px; height: 58px; border-radius: 50%;
    background: var(--teal); flex: none;
  }
  .brand__name {
    color: var(--teal); font-weight: 700;
    font-size: 25px; line-height: 1.15; letter-spacing: 0.5px;
    text-transform: uppercase;
  }
  .card--back {
    background: var(--teal);
    color: var(--white);
    padding: 42px 40px 34px;
  }
  .person__name { font-size: 19px; font-weight: 400; }
  .person__name strong { font-weight: 700; }
  .person__title { font-size: 13px; margin-top: 3px; }
  .address { font-size: 13px; line-height: 1.45; margin-top: 24px; }
  .contacts { list-style: none; margin-top: 18px; font-size: 12.5px; }
  .contacts li { display: flex; align-items: center; gap: 8px; margin-bottom: 5px; }
  .contacts svg { width: 15px; height: 15px; flex: none; }
  .back-brand {
    position: absolute; right: 40px; bottom: 30px;
    display: flex; align-items: center; gap: 10px;
  }
  .back-brand__dot { width: 22px; height: 22px; border-radius: 50%; background: var(--white); }
  .back-brand__name {
    font-size: 15px; font-weight: 700; letter-spacing: 0.5px;
    text-transform: uppercase; color: var(--white);
  }
</style>
</head>
<body>
<main class="stage">
  <section class="card card--front" aria-label="Card front">
    <div class="brand">
      <span class="brand__dot"></span>
      <p class="brand__name">Ridgeline<br>Pet Vision Care</p>
    </div>
  </section>

  <section class="card card--back" aria-label="Card back">
    <p class="person__name"><strong>Delia Vossman</strong>, BSc, DVM, MSc, DipACVO</p>
    <p class="person__title">Veterinary Ophthalmologist</p>
    <p class="address">1874 Thornbury Rd<br>Kelowna, BC, V1X 4M9</p>
    <ul class="contacts">
      <li>
        <svg viewBox="0 0 16 16" aria-hidden="true"><circle cx="8" cy="8" r="8" fill="#fff"/><path d="M5.2 4.2l1.3-.3 0.9 2-0.8 0.7a5 5 0 0 0 2.8 2.8l0.7-0.8 2 0.9-0.3 1.3c-3.6 0-6.9-3.3-6.6-6.6z" fill="#1597a8"/></svg>
        250.418.3927
      </li>
      <li>
        <svg viewBox="0 0 16 16" aria-hidden="true"><circle cx="8" cy="8" r="8" fill="#fff"/><rect x="4" y="5.2" width="8" height="5.6" rx="0.6" fill="none" stroke="#1597a8" stroke-width="1.1"/><path d="M4.3 5.6L8 8.4l3.7-2.8" fill="none" stroke="#1597a8" stroke-width="1.1"/></svg>
        ridgelinepetvisioncare@mailbox-example.net
      </li>
      <li>
        <svg viewBox="0 0 16 16" aria-hidden="true"><circle cx="8" cy="8" r="8" fill="#fff"/><circle cx="8" cy="8" r="4.2" fill="none" stroke="#1597a8" stroke-width="1"/><ellipse cx="8" cy="8" rx="1.8" ry="4.2" fill="none" stroke="#1597a8" stroke-width="0.9"/><path d="M3.8 8h8.4" stroke="#1597a8" stroke-width="0.9"/></svg>
        ridgelinepetvisioncare-example.net
      </li>
    </ul>
    <div class="back-brand">
      <span class="back-brand__dot"></span>
      <span class="back-brand__name">Ridgeline Pet Vision Care</span>
    </div>
  </section>
</main>
</body>
</html>
```